Namibia currently imports 60% of its food. Harvest Crest Oruva is an initiative which will assist Namibia to become self sustainable in terms of food production. We aim to do this through the development of 3 agricultural production zones which will include farming zones, local farmer assistance, processing and distribution of the final products. Please see our project overview attached.

```html
<!DOCTYPE html>
<html lang="en">
<head>
<meta charset="utf-8">
<title>Harvest Crest Oruva</title>
<link rel="stylesheet" href="https://fonts.googleapis.com/css2?family=Marcellus&family=Roboto:wght@300;400;500;700&display=swap">
<style>
:root{
  --green:#1b6d3b;
  --green-dark:#145a30;
  --green-soft:#9fd0b5;
  --gold:#c8a46c;
  --blue:#3a8fd0;
  --ink:#1d1d1d;
  --white:#ffffff;
}
*{box-sizing:border-box;margin:0;padding:0}
html,body{width:1200px;height:3924px;overflow:hidden;background:var(--white)}
body{position:relative;font-family:'Roboto',sans-serif;color:var(--ink)}
.abs{position:absolute}
.serif{font-family:'Marcellus',serif}
.btn{position:absolute;display:flex;align-items:center;justify-content:center;background:var(--green);color:var(--white);font-size:16px;font-weight:500;border-radius:0 12px 0 12px;text-transform:uppercase}
.btn.light{background:var(--white);color:var(--green-dark)}
.divider{position:absolute;display:flex;align-items:center;gap:14px}
.divider span{display:block;width:62px;height:2px;background:var(--gold)}
.divider i{display:block;width:14px;height:14px;border-radius:50%;background:var(--green)}
.divider.light span{background:var(--white)}
.divider.light i{background:var(--white)}

/* header */
.brand{left:111px;top:44px;font-family:'Marcellus',serif;font-size:30px;color:var(--green);letter-spacing:1px}
.brand small{display:block;font-size:12px;color:var(--gold);letter-spacing:6px;text-align:center;margin-top:-2px}
.nav{left:425px;top:52px;display:flex;gap:34px;font-size:16px;font-weight:500}
.nav a{color:var(--ink);text-decoration:none}
.nav a.active{color:var(--blue)}
.phone{left:905px;top:41px;display:flex;align-items:center;gap:12px;font-size:16px;font-weight:500}
.phone .dot{width:43px;height:43px;border-radius:50%;background:var(--green);display:flex;align-items:center;justify-content:center}

/* hero */
.welcome{left:111px;top:234px;font-size:32px;font-weight:300;color:var(--blue)}
.hero-title{left:109px;top:276px;font-size:62px;color:var(--green);line-height:1}
.hero-sub{left:111px;top:344px;font-size:32px;color:var(--gold);letter-spacing:10px}
.hero-copy{left:111px;top:392px;width:455px;font-size:16px;line-height:26px}
.arrow{position:absolute;width:30px;height:30px;border-radius:50%;border:1.5px solid var(--ink);display:flex;align-items:center;justify-content:center}
.arrow.fill{background:var(--ink)}
.hero-frame{left:585px;top:114px;width:489px;height:518px;background:var(--green);border-radius:130px 20px 220px 0}
.hero-photo{left:600px;top:126px;width:489px;height:517px;border-radius:120px 20px 210px 0;background:linear-gradient(180deg,#6f9cc9 0%,#a9c3d8 30%,#c9a04a 52%,#8a7a2c 75%,#3c4d7a 100%)}

/* solution */
.h2{position:absolute;font-family:'Marcellus',serif;font-size:34px;color:var(--green);white-space:nowrap}
.h2 em{font-style:normal;color:var(--gold)}
.solution-copy{left:257px;top:834px;width:686px;text-align:center;font-size:15.5px;line-height:28.5px}
.solution-copy b{color:var(--green);font-weight:500}
.card{position:absolute;width:300px;height:359px;border-radius:60px 0 70px 0;overflow:hidden;display:flex;align-items:flex-end;justify-content:center;padding-bottom:26px;color:var(--white);font-weight:700;font-size:20px;line-height:31px;text-align:center;text-transform:uppercase}
.card .pic{position:absolute;inset:0}
.card p{position:relative}

/* needs food */
.needs-frame{left:129px;top:1520px;width:473px;height:554px;background:var(--green);border-radius:20px 200px 0 200px}
.needs-photo{left:111px;top:1532px;width:475px;height:561px;border-radius:0 190px 20px 190px;background:linear-gradient(160deg,#7ea83c 0%,#4e7a2a 35%,#6b5a4a 60%,#c0843c 85%,#5a7a2a 100%)}
.needs-copy{left:641px;top:1692px;width:448px;font-size:15px;line-height:28.3px}

/* education */
.edu-band{left:0;top:2054px;width:1200px;height:843px;background:linear-gradient(180deg,#2e7a45 0%,#1f6a37 40%,#2b7b3e 70%,#1d5f30 100%)}
.edu-sub{left:280px;top:2283px;width:640px;text-align:center;color:var(--white);font-size:21px;line-height:29px;font-weight:400}
.edu-arrow{position:absolute;width:30px;height:30px;border-radius:50%;display:flex;align-items:center;justify-content:center}

/* sustainability */
.sus-frame{left:117px;top:2990px;width:980px;height:553px;background:var(--green);border-radius:200px 230px 20px 20px}
.sus-photo{left:134px;top:3003px;width:475px;height:552px;border-radius:190px 0 0 20px;background:linear-gradient(170deg,#4f7a3a 0%,#8a6a3a 45%,#d4a852 65%,#6a4a2a 100%)}
.sus-panel{left:576px;top:3003px;width:505px;height:552px;background:#24713f;border-radius:0 210px 0 200px}
.sus-title{left:576px;top:3070px;width:505px;text-align:center;color:var(--white);font-size:34px;line-height:45px}
.sus-kicker{left:576px;top:3220px;width:505px;text-align:center;color:var(--white);font-family:'Marcellus',serif;font-size:19px}
.sus-copy{left:586px;top:3258px;width:485px;text-align:center;color:var(--white);font-size:15px;line-height:28px}

/* footer */
.f-logo{left:111px;top:3650px;width:194px;height:120px;display:flex;align-items:center;justify-content:center;font-family:'Marcellus',serif;font-size:56px;color:var(--green)}
.socials{left:150px;top:3791px;display:flex;gap:12px}
.socials span{width:33px;height:33px;border-radius:50%;background:var(--ink)}
.f-head{position:absolute;font-size:20px;font-weight:500;text-transform:uppercase}
.f-links{left:343px;top:3692px;list-style:none;font-size:15px;line-height:30px}
.f-contact{left:521px;top:3704px;list-style:none;font-size:15px}
.f-contact li{display:flex;align-items:center;gap:10px;height:24px;margin-bottom:26px}
.email{left:769px;top:3704px;width:315px;height:43px;background:var(--green-soft);border-radius:0 12px 0 12px;padding:14px 10px;font-size:15px}
.copyright{left:0;top:3864px;width:1200px;text-align:center;font-size:15px}
</style>
</head>
<body>

<header>
  <div class="abs brand">HARVEST CREST<small>ORUVA</small></div>
  <nav class="abs nav">
    <a class="active" href="#">Home</a><a href="#">About</a><a href="#">Service</a><a href="#">Project</a><a href="#">Contact</a>
  </nav>
  <div class="abs phone">
    <span class="dot"><svg width="18" height="18" viewBox="0 0 24 24"><path fill="#fff" d="M6.6 10.8a15 15 0 0 0 6.6 6.6l2.2-2.2c.3-.3.7-.4 1-.2 1.1.4 2.3.6 3.6.6.6 0 1 .4 1 1V20c0 .6-.4 1-1 1A17 17 0 0 1 3 4c0-.6.4-1 1-1h3.5c.6 0 1 .4 1 1 0 1.3.2 2.5.6 3.6.1.3 0 .7-.2 1z"/></svg></span>
    +1(555) 014 2200
  </div>
</header>

<section class="hero">
  <div class="abs welcome">WELCOME TO</div>
  <h1 class="abs hero-title serif">HARVEST CREST</h1>
  <div class="abs hero-sub serif">ORUVA</div>
  <p class="abs hero-copy">Lorem ipsum dolor sit amet, consectetur adipiscing elit, eiusmod tempor incididunt ut labore et dolore magna aliqua. Quis ipsum suspendisse ultrices gravida.</p>
  <div class="btn" style="left:111px;top:486px;width:128px;height:39px">Get Started</div>
  <div class="arrow fill" style="left:112px;top:544px"><svg width="12" height="12" viewBox="0 0 12 12"><path d="M8 1 3 6l5 5" stroke="#fff" stroke-width="2" fill="none"/></svg></div>
  <div class="arrow" style="left:156px;top:544px"><svg width="12" height="12" viewBox="0 0 12 12"><path d="m4 1 5 5-5 5" stroke="#1d1d1d" stroke-width="1.5" fill="none"/></svg></div>
  <div class="abs hero-frame"></div>
  <div class="abs hero-photo" role="img" aria-label="Farmer in a bucket hat standing in a golden wheat field under a blue sky"></div>
</section>

<section class="solution">
  <h2 class="h2" style="left:0;width:1200px;text-align:center;top:736px">THE HARVEST CREST <em>SOLUTION</em></h2>
  <div class="divider" style="left:514px;top:793px"><span></span><i></i><span></span></div>
  <p class="abs solution-copy">The long term intention of the <b>Harvest Crest Oruva</b> program would be to establish 3 distinct food production and processing zones which have access to large amounts of arable land, with high quality soil and strong water resources, as well as good transport connections to relevant markets. They are:</p>
  <div class="card" style="left:111px;top:981px"><div class="pic" role="img" aria-label="Historic white building beside a river with flower beds" style="background:linear-gradient(180deg,#6f9fd6 0%,#dfe6ea 40%,#8a8a7a 65%,#a34a3a 85%,#3a4a3a 100%)"></div><p>Otavi Region<br>Central Namibia</p></div>
  <div class="card" style="left:451px;top:981px"><div class="pic" role="img" aria-label="Wide waterfall dropping into a misty gorge" style="background:linear-gradient(180deg,#8fb4d8 0%,#b8c7cf 30%,#6a7b6a 60%,#4a4a3a 100%)"></div><p>Kavango Region<br>North Namibia</p></div>
  <div class="card" style="left:789px;top:981px"><div class="pic" role="img" aria-label="Old stone weir house on a dam with flowing water" style="background:linear-gradient(180deg,#a7b4c2 0%,#6a6a5a 35%,#8a7c6a 55%,#4a5048 80%,#6a6a6a 100%)"></div><p>Neckartal Dam<br>South Namibia</p></div>
  <div class="btn" style="left:536px;top:1383px;width:128px;height:41px">Read More</div>
</section>

<section class="needs">
  <div class="abs needs-frame"></div>
  <div class="abs needs-photo" role="img" aria-label="Smiling farmer in an apron holding a crate of fresh vegetables"></div>
  <h2 class="h2" style="left:644px;top:1574px">NAMIBIA NEEDS <em>FOOD</em></h2>
  <div class="divider" style="left:643px;top:1637px"><span></span><i></i><span></span></div>
  <p class="abs needs-copy">Namibia is a young democracy in Sub-Saharan Africa with a population of approximately 2.5 Million people. The country's agricultural sector has been slow to keep up with the increasing population. As a consequence, approximately 60% of the food required to feed the nation is imported. The elevated cost of these imported foods means a large proportion of the population consume food with low nutritional value.</p>
  <div class="btn" style="left:646px;top:1908px;width:128px;height:41px">Read More</div>
</section>

<section class="education">
  <div class="abs edu-band" role="img" aria-label="Blurred green crop field background"></div>
  <h2 class="h2" style="left:0;width:1200px;text-align:center;top:2186px;color:#fff">“HARVEST CREST EDUCATION</h2>
  <div class="divider light" style="left:514px;top:2239px"><span></span><i></i><span></span></div>
  <p class="abs edu-sub">Give a man a fish and feed him for a day, teach a man to fish and feed him for a lifetime</p>
  <div class="edu-arrow" style="left:51px;top:2574px;background:#fff"><svg width="12" height="12" viewBox="0 0 12 12"><path d="M8 1 3 6l5 5" stroke="#1d1d1d" stroke-width="1.5" fill="none"/></svg></div>
  <div class="edu-arrow" style="left:1113px;top:2574px;border:1.5px solid #fff"><svg width="12" height="12" viewBox="0 0 12 12"><path d="m4 1 5 5-5 5" stroke="#fff" stroke-width="1.5" fill="none"/></svg></div>
  <div class="card" style="left:111px;top:2393px;height:357px"><div class="pic" role="img" aria-label="Long straight rows of young crops in a field" style="background:linear-gradient(180deg,#cdd6d0 0%,#6a8a3a 25%,#2f6a22 60%,#3a2a1a 100%)"></div><p>Farm Management</p></div>
  <div class="card" style="left:451px;top:2393px;height:357px"><div class="pic" role="img" aria-label="Red tractor spraying a green crop field" style="background:linear-gradient(180deg,#c9c0a8 0%,#7a8a5a 30%,#a34038 40%,#3f6a2a 65%,#2a4a1a 100%)"></div><p>Crop Management</p></div>
  <div class="card" style="left:789px;top:2393px;height:357px"><div class="pic" role="img" aria-label="Man with glasses working on a laptop against a white wall" style="background:linear-gradient(135deg,#eaeaea 0%,#d8d8d8 40%,#a8703a 60%,#3a3a44 100%)"></div><p>Business Management</p></div>
  <div class="btn light" style="left:536px;top:2788px;width:128px;height:42px">Read More</div>
</section>

<section class="sustain">
  <div class="abs sus-frame"></div>
  <div class="abs sus-photo" role="img" aria-label="Freshly harvested potatoes on soil with plants behind"></div>
  <div class="abs sus-panel"></div>
  <h2 class="abs sus-title serif">“HARVEST CREST”<br>SUSTAINABILITY</h2>
  <div class="divider light" style="left:743px;top:3173px"><span></span><i></i><span></span></div>
  <div class="abs sus-kicker">PROCESSING FACILITIES</div>
  <p class="abs sus-copy">Each of the allocated production zones will be furnished with handling, processing and milling facilities for all crops produced as part of the program. These will include Potatoes, Maize and Wheat.<br><span style="display:block;margin-top:12px">Harvest Crest Oruva will undertake primary production of the food goods and market them into the Namibian food supply chain.</span></p>
  <div class="btn light" style="left:763px;top:3436px;width:128px;height:41px">Read More</div>
</section>

<footer>
  <div class="abs f-logo">HCO</div>
  <div class="abs socials" aria-label="Social media links"><span></span><span></span><span></span></div>
  <div class="f-head" style="left:343px;top:3646px">Quick Links</div>
  <ul class="abs f-links"><li>Home</li><li>About</li><li>Service</li><li>Project</li><li>Contact</li></ul>
  <div class="f-head" style="left:521px;top:3646px">Contact Us</div>
  <ul class="abs f-contact">
    <li><svg width="20" height="16" viewBox="0 0 20 16"><rect width="20" height="16" rx="2" fill="#1b6d3b"/><path d="m2 3 8 6 8-6" stroke="#fff" stroke-width="1.6" fill="none"/></svg>hello@harvestcrestoruva.com</li>
    <li><svg width="18" height="18" viewBox="0 0 24 24"><path fill="#1b6d3b" d="M6.6 10.8a15 15 0 0 0 6.6 6.6l2.2-2.2c.3-.3.7-.4 1-.2 1.1.4 2.3.6 3.6.6.6 0 1 .4 1 1V20c0 .6-.4 1-1 1A17 17 0 0 1 3 4c0-.6.4-1 1-1h3.5c.6 0 1 .4 1 1 0 1.3.2 2.5.6 3.6.1.3 0 .7-.2 1z"/></svg>+1(555) 014 2200</li>
    <li><svg width="18" height="24" viewBox="0 0 18 24"><path fill="#1b6d3b" d="M9 0a9 9 0 0 0-9 9c0 7 9 15 9 15s9-8 9-15a9 9 0 0 0-9-9zm0 13a4 4 0 1 1 0-8 4 4 0 0 1 0 8z"/></svg>Harvest Crest,Oruva</li>
  </ul>
  <div class="f-head" style="left:766px;top:3646px">Subscribe to our Newsletter</div>
  <div class="abs email">Email</div>
  <div class="btn" style="left:769px;top:3763px;width:128px;height:41px">Subscribe</div>
  <p class="abs copyright">Copyright © 2024 Harvest Crest Oruva all rights reserved.</p>
</footer>

</body>
</html>
```